Web Design Project

i'm looking for a sleek modern design i can use for a web site that deals with.
Intelligent Data Capture
Accounts Payable Solutions for faster processing based on our scanning solution.
ultimately we are a intelligent scanning software.

here is a great website, that does exactly what we do, and we like to have most of their services and products.

so something in this idea would be great.
www.valtrino.com

so i guess i want a good landing/home page which is smartly designed so users will be inclined to leave their information.

and then information pages.

also i dont need any cms for you to include, i only need you to hook the html hooks for RANK Kettle as i already have a CMS and need it to hook in to that, i am including links to that cheat sheet.
so it is easier when included as you create the Theme.

http://www.rankkettle.com/how-to-create-website-template.html
http://www.rankkettle.com/cheat-sheet.html
Updates

Hi Guys sorry for the long pause in design, but here is where we stand.

what ever design i choose, i need that designer to customize a few things for me based on design that was designed.
and i will need designer to match that them to work with RANK Kettle
here is the cheat sheet for the hooks that we need to match and make it work.
if you have any questions let me know.

otherwise i look forward to working with you. and good luck.

Target Market(s)

CFO's AP Managers, mostly ppl who are not Tech freindly

Industry/Entity Type

Software

Requirements
Must have
• i need on home page, the rotating banner should have 1 ability to place youtube links to show videos, and also ability to add buttons on these rotating banners that will allow forms to pop up take to another page.

```html
<!DOCTYPE html>
<html lang="en">
<head>
<meta charset="utf-8">
<title>Norda — Intelligent Data Capture</title>
<link href="https://fonts.googleapis.com/css2?family=Ubuntu:wght@400;500;700&display=swap" rel="stylesheet">
<style>
:root{
  --blue:#0a66c2;
  --blue-deep:#0a4a8c;
  --blue-bright:#1a8cff;
  --nav-dark:#3d3d3d;
  --ink:#6b6b6b;
  --ink-soft:#8a8a8a;
  --heading:#6a6a6a;
  --link:#1060b0;
  --band:#efefef;
  --footer:#3b3b3b;
  --white:#ffffff;
}
*{box-sizing:border-box;margin:0;padding:0}
html,body{width:984px;height:1200px;overflow:hidden}
body{position:relative;font-family:'Ubuntu',sans-serif;background:var(--white);color:var(--ink)}
.abs{position:absolute}

.topbar{left:0;top:0;width:984px;height:30px;background:var(--blue)}
.search{left:573px;top:6px;width:195px;height:20px;background:var(--white);border:1px solid #c9d4e0;border-radius:2px;font-size:8px;color:#999;padding:5px 8px}
.search svg{position:absolute;right:6px;top:5px}
.toplinks{left:791px;top:11px;font-size:9px;color:var(--white);display:flex;gap:8px;align-items:center}
.flag{width:12px;height:8px;background:linear-gradient(#c33 0 2px,#fff 2px 4px,#c33 4px 6px,#fff 6px);position:relative}
.flag::before{content:"";position:absolute;left:0;top:0;width:5px;height:4px;background:#2a4a9a}

.navbar{left:0;top:30px;width:984px;height:42px;background:linear-gradient(#f6f6f6,#e2e2e2);border-bottom:2px solid var(--blue-deep)}
.brand{left:108px;top:34px;display:flex;align-items:center;gap:6px;color:var(--blue);font-weight:700;font-size:30px;letter-spacing:1px}
.brand i{display:block;width:26px;height:26px;border:3px solid var(--blue);border-radius:50%}
.nav{left:525px;top:30px;height:42px;display:flex}
.nav a{display:block;height:42px;padding:0 11px;line-height:48px;font-size:11px;font-weight:500;color:var(--blue-deep);text-decoration:none;border-left:1px solid #d6d6d6}
.nav a.current{background:var(--nav-dark);color:var(--white);padding:0 14px;border:none}

.hero{left:0;top:72px;width:984px;height:302px;background:radial-gradient(ellipse at 50% 100%,#1b8ef0 0,var(--blue) 55%,#0a5fb5 100%)}
.hero-shadow{left:110px;top:353px;width:767px;height:14px;background:radial-gradient(ellipse at 50% 0,rgba(0,20,60,.45),transparent 70%)}
.slide{left:110px;top:105px;width:767px;height:215px;background:#000;overflow:hidden}
.slide-art{left:0;top:0;width:560px;height:215px;
  background:
   radial-gradient(circle at 62% 45%,rgba(255,255,255,.9) 0,rgba(200,225,255,.5) 8%,transparent 22%),
   radial-gradient(ellipse at 10% 20%,#f1ecd0 0,transparent 30%),
   linear-gradient(100deg,#c9c4a6 0%,#7f96ae 22%,#3e4852 36%,#a9c2dc 50%,#6e8ea8 62%,#5a6e4c 74%,#222 88%,#000 100%)}
.slide-title{left:448px;top:130px;color:var(--white);font-size:26px;line-height:43px}
.slide-title b{color:var(--blue-bright);font-weight:500;font-size:34px}
.slide-bar{left:110px;top:320px;width:767px;height:33px;background:var(--blue-deep);display:flex;justify-content:center;align-items:center;gap:5px}
.slide-bar span{width:11px;height:11px;border-radius:50%;background:#222;border:2px solid #0c2a4a}
.slide-bar span.on{background:var(--blue-bright)}

h2{position:absolute;font-weight:500;font-size:16px;color:var(--heading)}
p.body{position:absolute;font-size:8.4px;line-height:11.9px;text-align:justify;color:var(--ink)}
a.more{position:absolute;font-size:9px;color:var(--link);text-decoration:underline;font-weight:500}
.ph{position:absolute}

.band{left:0;top:623px;width:984px;height:309px;background:var(--band)}
.icon{position:absolute}

.clients{left:107px;top:1036px;width:555px;display:flex;align-items:center;justify-content:space-between}
.clients .arrow{color:#bbb;font-size:22px}
.clients span.c{display:flex;align-items:center;gap:4px;font-size:8px;font-weight:500;color:#444}
.clients span.c i{display:block;width:12px;height:12px;border-radius:50%;background:#333}
.clients span.c1{color:#1a6fc0}.clients span.c1 i{background:#1a6fc0;border-radius:2px}
.clients span.c2{color:#e07a10}.clients span.c2 i{background:#e07a10}
.clients span.c3{color:#6aa84f}.clients span.c3 i{background:#6aa84f;border-radius:2px}
.quote{left:680px;top:1016px;width:198px;font-size:8.4px;line-height:11.9px;color:var(--ink-soft);text-align:justify}
.sig{left:680px;top:1086px;font-size:8.4px;color:var(--ink-soft)}
.tnav{left:858px;top:987px;color:#bbb;font-size:12px;letter-spacing:2px}

.footer{left:0;top:1116px;width:984px;height:84px;background:var(--footer)}
.social{left:107px;top:1145px;display:flex;gap:5px}
.social span{width:24px;height:24px;border-radius:50%;background:var(--white);color:var(--footer);font-size:6px;font-weight:700;display:flex;align-items:center;justify-content:center}
.flinks{left:500px;top:1137px;width:378px;text-align:right;font-size:8.6px;color:var(--white);word-spacing:2px}
.copy{left:500px;top:1158px;width:378px;text-align:right;font-size:8.6px;color:var(--white)}
</style>
</head>
<body>
<div class="abs topbar"></div>
<div class="abs search">Search
  <svg width="9" height="9" viewBox="0 0 9 9"><circle cx="3.5" cy="3.5" r="2.6" fill="none" stroke="#aaa"/><line x1="5.5" y1="5.5" x2="8.5" y2="8.5" stroke="#aaa"/></svg>
</div>
<div class="abs toplinks"><span class="flag"></span><span>▾</span><span>Help</span><span>Log in</span></div>

<div class="abs navbar"></div>
<div class="abs brand"><i></i>NORDA</div>
<nav class="abs nav">
  <a class="current">HOME</a><a>ABOUT US</a><a>SERVICES</a><a>CLIENTS</a><a>CONTACT US</a>
</nav>

<section class="abs hero"></section>
<div class="abs hero-shadow"></div>
<div class="abs slide">
  <div class="abs slide-art" role="img" aria-label="Hand reaching toward a stream of floating photo panels"></div>
  <div class="abs slide-title">Intelligent data capture<br>from <b>Online Sites</b></div>
</div>
<div class="abs slide-bar"><span class="on"></span><span></span><span></span></div>

<h2 style="left:107px;top:398px">Welcome to norda data capture</h2>
<div class="ph" style="left:106px;top:433px;width:174px;height:145px;background:radial-gradient(ellipse at 55% 55%,#e8f2ff 0,#7fb4f2 18%,#2a62d8 45%,#0a2580 80%,#061650 100%)" role="img" aria-label="Person touching a glowing wall of binary digits"></div>
<p class="body" style="left:303px;top:439px;width:269px">Mauris vel lacus vitae felis vestibulum volutpat. Etiam est nunc, venenatis in, tristique eu, imperdiet ac, nisl. Cum sociis natoque penatibus et magnis dis parturient montes, nascetur ridiculus mus. In iaculis facilisis massa. Etiam eu urna. Sed porta. Suspendisse quam leo, molestie sed, luctus quis, feugiat in, pede. Fusce tellus. Sed metus augue, convallis et, vehicula ut, pulvinar eu, ante. Integer orci tellus, tristique vitae, consequat nec, porta vel, lectus. Nulla sit amet diam. Duis non nunc. Nulla rhoncus dictum metus. Curabitur tristique mi condimentum orci. Phasellus pellentesque aliquam enim. Proin dui lectus, cursus eu, mattis laoreet, viverra sit amet, quam.</p>
<a class="more" style="left:526px;top:590px">Read more</a>

<h2 style="left:597px;top:398px">How it works</h2>
<div class="ph" style="left:598px;top:433px;width:280px;height:154px;background:radial-gradient(ellipse at 50% 70%,#3a3f4a 0,#6a6e76 25%,#cfd2d6 55%,#f3f3f3 100%)" role="img" aria-label="Video still: excited businessman holding a tablet"></div>
<svg class="ph" style="left:713px;top:498px" width="28" height="28" viewBox="0 0 28 28"><polygon points="7,3 25,14 7,25" fill="#fff" opacity=".9"/></svg>
<div class="ph" style="left:598px;top:587px;width:280px;height:14px;background:#1a1a1a"></div>
<div class="ph" style="left:598px;top:585px;width:280px;height:2px;background:#555"></div>
<div class="ph" style="left:598px;top:585px;width:120px;height:2px;background:#d00"></div>
<div class="ph" style="left:715px;top:583px;width:6px;height:6px;border-radius:50%;background:#ddd"></div>
<svg class="ph" style="left:607px;top:590px" width="6" height="7"><polygon points="0,0 6,3.5 0,7" fill="#ddd"/></svg>
<svg class="ph" style="left:624px;top:590px" width="8" height="7"><polygon points="0,2 2,2 5,0 5,7 2,5 0,5" fill="#ddd"/></svg>
<span class="ph" style="left:642px;top:590px;font-size:5px;color:#ddd">0:13 / 0:31</span>
<span class="ph" style="left:850px;top:590px;font-size:5px;color:#ddd">360p</span>
<div class="ph" style="left:866px;top:590px;width:7px;height:6px;border:1px solid #ddd"></div>

<section class="abs band"></section>

<svg class="icon" style="left:106px;top:626px" width="26" height="30" viewBox="0 0 26 30"><circle cx="10" cy="10" r="7" fill="none" stroke="var(--blue)" stroke-width="4" stroke-dasharray="3 2"/><circle cx="10" cy="10" r="3" fill="var(--blue)"/><circle cx="20" cy="23" r="3.5" fill="none" stroke="var(--blue)" stroke-width="2.5"/></svg>
<h2 style="left:148px;top:633px">Our Services</h2>
<svg class="icon" style="left:395px;top:628px" width="30" height="26" viewBox="0 0 30 26"><rect x="1" y="6" width="19" height="19" fill="none" stroke="var(--blue)" stroke-width="2"/><polyline points="5,13 11,20 28,2" fill="none" stroke="var(--blue)" stroke-width="4"/></svg>
<h2 style="left:439px;top:631px">Our Advantages</h2>
<svg class="icon" style="left:688px;top:623px" width="18" height="38" viewBox="0 0 18 38"><path d="M9 2c-5 0-8 4-8 8 0 4 3 6 4 9v5h8v-5c1-3 4-5 4-9 0-4-3-8-8-8z" fill="var(--blue)"/><rect x="5" y="26" width="8" height="3" fill="var(--blue)"/><rect x="6" y="31" width="6" height="3" fill="var(--blue)"/></svg>
<h2 style="left:721px;top:631px">Our Expertise</h2>

<div class="ph" style="left:107px;top:663px;width:196px;height:123px;background:linear-gradient(#6d84a0 0%,#a9bbd0 25%,#eef2f6 55%,#9aa8b8 75%,#1c2430 100%)" role="img" aria-label="Silhouetted business people in front of a world map"></div>
<div class="ph" style="left:395px;top:663px;width:196px;height:123px;background:radial-gradient(ellipse at 60% 35%,#f3d9c2 0,#d8a888 18%,transparent 40%),linear-gradient(160deg,#eaf5fd 0%,#9cc7ec 40%,#2d6cb8 75%,#153e80 100%)" role="img" aria-label="Team stacking hands together"></div>
<div class="ph" style="left:680px;top:663px;width:198px;height:123px;background:radial-gradient(ellipse at 50% 45%,#fffbe8 0,#e8dcb0 10%,#8a7a58 30%,#3a3226 55%,#16130f 85%)" role="img" aria-label="Row of light bulbs with one glowing"></div>

<p class="body" style="left:107px;top:794px;width:196px">Lorem ipsum dolor sit amet, consectetuer adipiscing elit. Nam cursus. Morbi ut mi. Nullam enim leo, egestas id, condimentum at, laoreet mattis, massa. Sed eleifend nonummy diam. Praesent mauris ante, elementum et, bibendum at, posuere sit amet, nibh. Duis tincidunt lectus quis dui viverra vestibulum. Suspendisse vulputate aliquam dui. Nulla elementum dui ut augue.</p>
<p class="body" style="left:395px;top:794px;width:196px">Lorem ipsum dolor sit amet, consectetuer adipiscing elit. Nam cursus. Morbi ut mi. Nullam enim leo, egestas id, condimentum at, laoreet mattis, massa. Sed eleifend nonummy diam. Praesent mauris ante, elementum et, bibendum at, posuere sit amet, nibh. Duis tincidunt lectus quis dui viverra vestibulum. Suspendisse vulputate aliquam dui. Nulla elementum dui ut augue.</p>
<p class="body" style="left:680px;top:794px;width:198px">Lorem ipsum dolor sit amet, consectetuer adipiscing elit. Nam cursus. Morbi ut mi. Nullam enim leo, egestas id, condimentum at, laoreet mattis, massa. Sed eleifend nonummy diam. Praesent mauris ante, elementum et, bibendum at, posuere sit amet, nibh. Duis tincidunt lectus quis dui viverra vestibulum. Suspendisse vulputate aliquam dui. Nulla elementum dui ut augue.</p>
<a class="more" style="left:257px;top:900px">Read more</a>
<a class="more" style="left:545px;top:900px">Read more</a>
<a class="more" style="left:830px;top:900px">Read more</a>

<h2 style="left:107px;top:983px">Our Clients</h2>
<div class="abs clients">
  <span class="arrow">‹</span>
  <span class="c"><i></i>lumenrow</span>
  <span class="c c1"><i></i>Orvella</span>
  <span class="c c2"><i></i>Harbor Link</span>
  <span class="c"><i></i>Pantry Loop</span>
  <span class="c"><i></i>Fibre Co</span>
  <span class="c">m.valdek</span>
  <span class="c c3"><i></i>tarrow</span>
  <span class="arrow">›</span>
</div>

<h2 style="left:680px;top:983px">Testimonials</h2>
<div class="abs tnav">‹›</div>
<p class="abs quote">"Scanfieldcapture.com team understands there job and specialize in what they do. There is clarity in understanding and perfect ness in execution. I would recommend services and expertise to any business."</p>
<div class="abs sig">- CEO of a leading USA Company</div>

<footer class="abs footer"></footer>
<div class="abs social" aria-label="Social links"><span>Chirp</span><span>Linkd</span><span>Facet</span><span>Feed</span></div>
<div class="abs flinks">Home &nbsp;About us &nbsp;Terms &amp; Conditions &nbsp;Privacy Policy &nbsp;Contact us</div>
<div class="abs copy">Copyright © 2012 Norda,All Rights Reserved</div>
</body>
</html>
```